Real Estate Brokerage Stationery Designs

I am looking to have presentation folders with business card slots on both sides along with pockets on both sides. I've attached logos, website colors along with current business card designs.

I am looking for envelope designs both big and small. Possibly new business card designs, notepad templates for big and small notepads. Letterhead designs. Pop socket designs. Realtors name badge designs.

www.brightholdrealty.example

```html
<!DOCTYPE html>
<html lang="en">
<head>
<meta charset="utf-8">
<title>Brighthold Realty — Presentation Folder</title>
<link href="https://fonts.googleapis.com/css2?family=Roboto:wght@400;500&display=swap" rel="stylesheet">
<style>
  :root {
    --backdrop: #b4b4b4;
    --brand-blue: #0d56a6;
    --brand-blue-deep: #08478f;
    --brand-blue-light: #2f74bb;
    --paper: #f3f3f3;
    --paper-shade: #e4e4e4;
    --ink: #2b2b2b;
    --muted: #9a9a9a;
    --faint-on-blue: rgba(255,255,255,0.09);
    --faint-on-paper: rgba(13,86,166,0.07);
  }
  * { box-sizing: border-box; margin: 0; padding: 0; }
  html, body { width: 842px; height: 1200px; overflow: hidden; }
  body {
    background: var(--backdrop);
    font-family: "Roboto", Arial, sans-serif;
    position: relative;
  }
  .spread {
    position: absolute;
    left: 51px;
    width: 740px;
    height: 520px;
    display: flex;
    box-shadow: 0 10px 26px rgba(0,0,0,0.25);
  }
  .spread--outside { top: 40px; }
  .spread--inside { top: 630px; }
  .panel {
    position: relative;
    width: 370px;
    height: 100%;
    overflow: hidden;
  }
  /* outside */
  .panel--back {
    background: linear-gradient(160deg, var(--brand-blue-deep), var(--brand-blue) 55%, var(--brand-blue-deep));
  }
  .panel--front {
    background: linear-gradient(200deg, #fbfbfb, var(--paper) 60%, var(--paper-shade));
  }
  .watermark-name {
    position: absolute;
    left: 30px;
    top: 170px;
    width: 310px;
    font-weight: 500;
    font-size: 54px;
    line-height: 1.05;
    color: var(--faint-on-blue);
  }
  .contact {
    position: absolute;
    left: 0;
    right: 0;
    bottom: 30px;
    text-align: center;
    color: #dbe7f5;
    font-size: 7.5px;
    line-height: 1.6;
  }
  .contact .rule-line {
    display: flex;
    align-items: center;
    justify-content: center;
    gap: 8px;
  }
  .contact .rule-line::before,
  .contact .rule-line::after {
    content: "";
    width: 34px;
    height: 1px;
    background: #dbe7f5;
  }
  .brand {
    position: absolute;
    left: 0;
    right: 0;
    top: 205px;
    display: flex;
    align-items: center;
    justify-content: center;
    gap: 12px;
  }
  .brand__square {
    width: 26px;
    height: 26px;
    background: var(--brand-blue);
  }
  .brand__name {
    font-weight: 500;
    font-size: 30px;
    color: var(--ink);
    letter-spacing: 0.5px;
  }
  /* inside */
  .panel--inside {
    background: linear-gradient(180deg, #fafafa, var(--paper));
  }
  .panel--inside + .panel--inside { border-left: 1px solid #dcdcdc; }
  .inside-watermark {
    position: absolute;
    left: 30px;
    top: 60px;
    width: 310px;
    font-weight: 500;
    font-size: 48px;
    line-height: 1.05;
    color: var(--faint-on-paper);
  }
  .pocket {
    position: absolute;
    left: 0;
    bottom: 0;
    width: 100%;
    height: 210px;
    background: linear-gradient(170deg, var(--brand-blue-deep), var(--brand-blue-light));
    box-shadow: 0 -4px 10px rgba(0,0,0,0.18);
  }
  .card-slot {
    position: absolute;
    top: 52px;
    width: 120px;
    height: 70px;
  }
  .pocket--left .card-slot { left: 200px; }
  .pocket--right .card-slot { left: 50px; }
</style>
</head>
<body>
  <section class="spread spread--outside" aria-label="Folder outside">
    <div class="panel panel--back">
      <div class="watermark-name" aria-hidden="true">Brighthold Realty</div>
      <div class="contact">
        <p>P: 555-201-4800 &nbsp;C: 555-201-4811</p>
        <p>F: 555-201-4822 &nbsp;E: hello@brightholdrealty.example &nbsp;W: www.brightholdrealty.example</p>
        <p class="rule-line">200 Harbor Way, Suite 12, Lakeview, FL 30000</p>
      </div>
    </div>
    <div class="panel panel--front">
      <div class="brand">
        <span class="brand__square"></span>
        <span class="brand__name">Brighthold Realty</span>
      </div>
    </div>
  </section>

  <section class="spread spread--inside" aria-label="Folder inside">
    <div class="panel panel--inside">
      <div class="inside-watermark" aria-hidden="true">Brighthold Realty</div>
      <div class="pocket pocket--left">
        <svg class="card-slot" viewBox="0 0 120 70" aria-hidden="true">
          <path d="M0 0 L18 0 M0 0 L0 18 M120 70 L102 70 M120 70 L120 52" stroke="#cfe0f2" stroke-width="2" fill="none"/>
        </svg>
      </div>
    </div>
    <div class="panel panel--inside">
      <div class="inside-watermark" aria-hidden="true">Brighthold Realty</div>
      <div class="pocket pocket--right">
        <svg class="card-slot" viewBox="0 0 120 70" aria-hidden="true">
          <path d="M0 0 L18 0 M0 0 L0 18 M120 70 L102 70 M120 70 L120 52" stroke="#cfe0f2" stroke-width="2" fill="none"/>
        </svg>
      </div>
    </div>
  </section>
</body>
</html>
```